Graphics for New Online Software

Looking at a designer to design a UI/UX Interface for an Online Events Platform (just JPEG) and some corresponding images for a website content (i.e. features etc)

Deliverables:
1x User Interface Design for the Platform (refer to attachment)
5-6x Feature Listing Images (refer to attachment)

Target Market(s)

Technology, Online Users Etc

Industry/Entity Type

Software Developer

Number of Pages Required

1 page

Font styles to use
Sans Serif

Colors
34a7d8
0493ce
3176b5
85acd3

Requirements
Must have
• Looks like a well built software - examples:
https://gravelmoor.io/
https://quintaro.com/

All the images should look very professional, as though you are using it on the online platform itself.
Nice to have
• Refer to attached "Feature Listing" and Logo

```html
<!DOCTYPE html>
<html lang="en">
<head>
<meta charset="utf-8">
<title>Nexavent – Online Events Platform</title>
<link href="https://fonts.googleapis.com/css2?family=Quicksand:wght@500;600;700&family=Montserrat:wght@800&display=swap" rel="stylesheet">
<style>
:root{
  --bg:#e9e9ea;
  --panel:#ffffff;
  --side:#e4e3e4;
  --side-active:#d6d2d4;
  --ink:#1c1a2e;
  --text:#333333;
  --muted:#777777;
  --line:#d9d9d9;
  --blue:#3176b5;
  --sky:#34a7d8;
  --cyan:#0493ce;
  --soft:#85acd3;
  --accent:#3a7de0;
  --alert:#e8322c;
  --bar:#000000;
}
*{box-sizing:border-box;margin:0;padding:0}
html,body{width:1200px;height:2668px;overflow:hidden}
body{background:var(--bg);font-family:"Quicksand",sans-serif;color:var(--text);position:relative}
.brand{font-family:"Montserrat",sans-serif;font-weight:800;color:var(--ink);letter-spacing:-1px;display:flex;align-items:center;gap:10px}
.brand .mark{width:16px;height:16px;background:var(--accent)}
.hero-brand{position:absolute;top:46px;left:0;width:1200px;justify-content:center;font-size:52px}
.hero-brand .mark{width:26px;height:26px}
.app{position:absolute;left:105px;width:990px;background:var(--panel);box-shadow:0 6px 24px rgba(0,0,0,.12);overflow:hidden}
.app-1{top:196px;height:619px}
.app-2{top:1170px;height:660px}
.app-3{top:1920px;height:660px}
.sidebar{position:absolute;left:0;top:0;bottom:0;width:242px;background:var(--side);border-top-right-radius:56px}
.sidebar .brand{position:absolute;left:16px;top:24px;font-size:31px}
.sidebar .rule{position:absolute;left:28px;right:30px;top:84px;border-top:1px solid #c9c9c9}
.nav-title{position:absolute;top:102px;width:100%;text-align:center;font-size:11px;letter-spacing:1.2px;color:var(--accent);font-weight:600}
.nav{position:absolute;top:129px;left:0;width:100%;list-style:none}
.nav li{height:79.5px;display:flex;flex-direction:column;align-items:center;justify-content:center;gap:4px;font-size:13px;color:var(--text)}
.nav li.active{background:var(--side-active)}
.nav svg{width:34px;height:32px;fill:none;stroke:var(--blue);stroke-width:1.4}
.topbar{position:absolute;left:270px;right:30px;top:0;height:84px;border-bottom:1px solid var(--line)}
.tools{position:absolute;right:0;top:26px;display:flex;align-items:center}
.tool{position:relative;width:24px;height:24px;margin-right:22px}
.tool svg{width:22px;height:22px;fill:#5a5a5a}
.tool .badge{position:absolute;right:-3px;top:-5px;width:10px;height:10px;border-radius:50%;background:var(--alert);color:#fff;font-size:6px;text-align:center;line-height:10px}
.user{display:flex;align-items:center;gap:12px;font-size:13px;color:#444;margin-left:24px}
.avatar{width:36px;height:36px;border-radius:50%;background:linear-gradient(#6d5a4c,#c7a08a);position:relative}
.avatar::after{content:"";position:absolute;right:0;bottom:1px;width:8px;height:8px;border-radius:50%;background:#3bc45e;border:1px solid #fff}
.caret{width:0;height:0;border:4px solid transparent;border-top-color:#555;margin-top:4px;margin-left:4px}
.duration{position:absolute;right:30px;top:99px;font-size:12px;color:var(--ink)}
.media{position:absolute;left:270px;width:689px;display:flex;align-items:center;justify-content:center}
.media-video{top:131px;height:404px;background:radial-gradient(circle at 55% 45%,#caa48c 0,#8f7a70 28%,#4a4f5c 55%,#2c3038 100%)}
.media-expo{top:130px;height:404px;background:linear-gradient(135deg,#f2f3f7 0%,#dfe6f5 40%,#9fb8ea 70%,#5b86e0 100%)}
.play{width:36px;height:36px;border-radius:50%;background:#fff;display:flex;align-items:center;justify-content:center}
.play.dark{background:#000}
.play::after{content:"";border-left:12px solid #222;border-top:8px solid transparent;border-bottom:8px solid transparent;margin-left:4px}
.play.dark::after{border-left-color:#fff}
.controls{position:absolute;left:270px;width:689px;top:535px;height:60px;background:var(--bar);display:flex;color:#fff;font-size:10px;padding:0 6px}
.ctl{width:70px;display:flex;flex-direction:column;align-items:center;justify-content:center;gap:5px}
.ctl svg{width:14px;height:14px;fill:#fff}
.ctl.wide{width:86px}
.spacer{flex:1}
.speakers{position:absolute;left:270px;top:130px;width:434px;display:grid;grid-template-columns:200px 200px;column-gap:34px;row-gap:26px}
.speaker .photo{height:165px;background:linear-gradient(#c9c9cb,#8d8f94)}
.speaker .photo.dark{background:linear-gradient(#6a6a6e,#3b3b40)}
.speaker a{display:block;margin-top:10px;font-size:10px;line-height:15px;color:var(--accent)}
.chat{position:absolute;left:742px;top:90px;bottom:40px;border-left:1px solid var(--line);padding-left:28px;width:248px}
.tabs{display:flex;justify-content:space-between;width:194px;border-bottom:1px solid var(--line);font-size:12px;color:var(--ink);padding:14px 10px 10px 6px;position:relative}
.tabs .on{position:relative}
.tabs .on::after{content:"";position:absolute;left:-6px;right:-10px;bottom:-11px;border-bottom:2px solid var(--accent)}
.msg{margin-top:24px;width:184px}
.msg+.msg{margin-top:16px}
.msg-head{display:flex;align-items:center;gap:8px;font-size:12px;color:var(--ink)}
.msg-head .face{width:30px;height:30px;border-radius:50%;background:linear-gradient(#8a6d5c,#d4b5a0)}
.msg-head time{margin-left:auto;font-size:8px;color:var(--muted)}
.msg p{font-size:7.5px;line-height:13px;color:#444;margin-top:6px}
.composer{display:flex;margin-top:26px;width:194px;height:36px}
.composer span{flex:1;background:#efefef;font-size:11px;color:#666;padding:11px 13px}
.composer b{width:35px;background:var(--sky);display:flex;align-items:center;justify-content:center}
.composer svg{width:14px;height:14px;fill:none;stroke:#fff;stroke-width:1.6}
.copy{position:absolute;left:242px;right:0;bottom:8px;text-align:center;font-size:9px;color:#444}
.caption{position:absolute;left:270px;top:563px;font-size:10px;color:var(--ink);line-height:19px}
.caption a{color:var(--accent)}
.cta{position:absolute;left:844px;top:559px;width:115px;height:31px;background:var(--sky);color:#fff;font-size:11px;display:flex;align-items:center;justify-content:center}
</style>
</head>
<body>

<div class="brand hero-brand">NEXAVENT<span class="mark"></span></div>

<!-- Stage view -->
<section class="app app-1">
  <aside class="sidebar">
    <div class="brand">NEXAVENT<span class="mark"></span></div>
    <div class="rule"></div>
    <div class="nav-title">MAIN NAVIGATION</div>
    <ul class="nav">
      <li class="active"><svg viewBox="0 0 34 32"><rect x="3" y="5" width="28" height="24" rx="2"/><path d="M3 11h28M10 2v6M24 2v6M9 16h3M16 16h3M23 16h3M9 22h3M16 22h3M23 22h3"/></svg>Event Info</li>
      <li><svg viewBox="0 0 34 32"><rect x="3" y="3" width="28" height="26"/><path d="M3 3c4 8 6 14 4 26M31 3c-4 8-6 14-4 26M17 13l2 4 4 .5-3 3 1 4-4-2-4 2 1-4-3-3 4-.5z"/></svg>Stage</li>
      <li><svg viewBox="0 0 34 32"><rect x="16" y="3" width="15" height="12"/><path d="M3 29h28M6 29v-9h22v9M5 20v-8l4-6 3 6M20 7l6 5"/></svg>Breakouts</li>
      <li><svg viewBox="0 0 34 32"><path d="M3 5l7 3v20l-7-3zM31 5l-7 3v20l7-3z"/><rect x="11" y="9" width="12" height="12"/><path d="M17 21v7M13 28h8"/></svg>Virtual Exhibition</li>
      <li><svg viewBox="0 0 34 32"><rect x="10" y="3" width="14" height="12"/><circle cx="17" cy="9" r="3"/><path d="M17 15v6M4 29l5-8h16l5 8z"/></svg>Booths</li>
      <li><svg viewBox="0 0 34 32"><path d="M11 3h12l-3 7h-6z"/><circle cx="17" cy="20" r="10"/><path d="M17 14l2 4 4 .5-3 3 1 4-4-2-4 2 1-4-3-3 4-.5z"/></svg>Rewards</li>
    </ul>
  </aside>
  <header class="topbar">
    <div class="tools">
      <div class="tool"><svg viewBox="0 0 24 24"><path d="M12 22a2.5 2.5 0 0 0 2.5-2.5h-5A2.5 2.5 0 0 0 12 22zm7-6V11a7 7 0 0 0-5.5-6.8V3a1.5 1.5 0 0 0-3 0v1.2A7 7 0 0 0 5 11v5l-2 2v1h18v-1z"/></svg><span class="badge">5</span></div>
      <div class="tool"><svg viewBox="0 0 24 24"><path d="M3 5h18v12H8l-5 4z"/></svg><span class="badge">8</span></div>
      <div class="user"><span class="avatar" role="img" aria-label="User profile photo"></span>Jane.s<span class="caret"></span></div>
    </div>
  </header>
  <div class="duration">Event Duration (Remaining HH:MM)</div>
  <div class="media media-video" role="img" aria-label="Live video of a smiling presenter in a suit"><span class="play"></span></div>
  <div class="controls">
    <div class="ctl"><svg viewBox="0 0 14 14"><rect x="5" y="1" width="4" height="8" rx="2"/><path d="M3 7a4 4 0 0 0 8 0h1a5 5 0 0 1-4.5 5V14h-1v-2A5 5 0 0 1 2 7z"/></svg>Mute</div>
    <div class="ctl wide"><svg viewBox="0 0 14 14"><rect x="1" y="3" width="9" height="8" rx="1"/><path d="M10 6l3-2v6l-3-2z"/></svg>Start Video</div>
    <div class="spacer"></div>
    <div class="ctl"><svg viewBox="0 0 14 14"><circle cx="6" cy="4" r="3"/><path d="M0 13a6 5 0 0 1 12 0zM11 5h1v2h2v1h-2v2h-1V8H9V7h2z"/></svg>Invite</div>
    <div class="ctl wide"><svg viewBox="0 0 14 14"><circle cx="7" cy="4" r="2.5"/><circle cx="2.5" cy="5" r="1.8"/><circle cx="11.5" cy="5" r="1.8"/><path d="M2 13a5 4 0 0 1 10 0zM0 11a3 3 0 0 1 3-3l1 1-2 2zM14 11a3 3 0 0 0-3-3l-1 1 2 2z"/></svg>Participants</div>
    <div class="ctl"><svg viewBox="0 0 14 14"><path d="M1 4h5v1.5H2.5v6h8V9H12v4H1zM8 1l5 4-5 4V7C6 7 4.5 8 4 10 4 6 6 4.5 8 4.5z"/></svg>Share</div>
    <div class="ctl"><svg viewBox="0 0 14 14"><path d="M7 1c3.9 0 7 2.4 7 5.4S10.9 12 7 12l-4 2 1-3C1.6 10 0 8.4 0 6.4 0 3.4 3.1 1 7 1z"/></svg>Chat</div>
    <div class="ctl"><svg viewBox="0 0 14 14"><path d="M7 0a7 7 0 1 1 0 14A7 7 0 0 1 7 0zm0 1.6a5.4 5.4 0 1 0 0 10.8A5.4 5.4 0 0 0 7 1.6z"/><circle cx="7" cy="7" r="2.6"/></svg>Reserved</div>
  </div>
</section>

<!-- Booths view -->
<section class="app app-2">
  <aside class="sidebar">
    <div class="brand">NEXAVENT<span class="mark"></span></div>
    <div class="rule"></div>
    <div class="nav-title">MAIN NAVIGATION</div>
    <ul class="nav">
      <li><svg viewBox="0 0 34 32"><rect x="3" y="5" width="28" height="24" rx="2"/><path d="M3 11h28M10 2v6M24 2v6M9 16h3M16 16h3M23 16h3M9 22h3M16 22h3M23 22h3"/></svg>Event Info</li>
      <li><svg viewBox="0 0 34 32"><rect x="3" y="3" width="28" height="26"/><path d="M3 3c4 8 6 14 4 26M31 3c-4 8-6 14-4 26M17 13l2 4 4 .5-3 3 1 4-4-2-4 2 1-4-3-3 4-.5z"/></svg>Stage</li>
      <li><svg viewBox="0 0 34 32"><rect x="16" y="3" width="15" height="12"/><path d="M3 29h28M6 29v-9h22v9M5 20v-8l4-6 3 6M20 7l6 5"/></svg>Breakouts</li>
      <li><svg viewBox="0 0 34 32"><path d="M3 5l7 3v20l-7-3zM31 5l-7 3v20l7-3z"/><rect x="11" y="9" width="12" height="12"/><path d="M17 21v7M13 28h8"/></svg>Virtual Exhibition</li>
      <li class="active"><svg viewBox="0 0 34 32"><rect x="10" y="3" width="14" height="12"/><circle cx="17" cy="9" r="3"/><path d="M17 15v6M4 29l5-8h16l5 8z"/></svg>Booths</li>
      <li><svg viewBox="0 0 34 32"><path d="M11 3h12l-3 7h-6z"/><circle cx="17" cy="20" r="10"/><path d="M17 14l2 4 4 .5-3 3 1 4-4-2-4 2 1-4-3-3 4-.5z"/></svg>Rewards</li>
    </ul>
  </aside>
  <header class="topbar">
    <div class="tools">
      <div class="tool"><svg viewBox="0 0 24 24"><path d="M12 22a2.5 2.5 0 0 0 2.5-2.5h-5A2.5 2.5 0 0 0 12 22zm7-6V11a7 7 0 0 0-5.5-6.8V3a1.5 1.5 0 0 0-3 0v1.2A7 7 0 0 0 5 11v5l-2 2v1h18v-1z"/></svg><span class="badge">5</span></div>
      <div class="tool"><svg viewBox="0 0 24 24"><path d="M3 5h18v12H8l-5 4z"/></svg><span class="badge">8</span></div>
      <div class="user"><span class="avatar" role="img" aria-label="User profile photo"></span>Jane.s<span class="caret"></span></div>
    </div>
  </header>
  <div class="duration" style="right:287px">Event Duration (Remaining HH:MM)</div>
  <div class="speakers">
    <div class="speaker"><div class="photo" role="img" aria-label="Portrait of a smiling woman in a grey blazer"></div><a>Lorem ipsum dolor sit amet, consectetur adipiscing elit,</a></div>
    <div class="speaker"><div class="photo dark" role="img" aria-label="Portrait of a smiling man in a dark suit"></div><a>Lorem ipsum dolor sit amet, consectetur adipiscing elit,</a></div>
    <div class="speaker"><div class="photo" role="img" aria-label="Portrait of a smiling man with crossed arms"></div><a>Lorem ipsum dolor sit amet, consectetur adipiscing elit,</a></div>
    <div class="speaker"><div class="photo" role="img" aria-label="Portrait of a smiling woman in a white blouse"></div><a>Lorem ipsum dolor sit amet, consectetur adipiscing elit,</a></div>
  </div>
  <div class="chat">
    <div class="tabs"><span class="on">Chat</span><span>Q&amp;A</span><span>Poll</span></div>
    <div class="msg"><div class="msg-head"><span class="face" role="img" aria-label="Attendee photo"></span>Kategreen<time>6 min ago</time></div><p>Lorem ipsum dolor sit amet, consectetur ing elit, sed do eiusmod tempor incididunt ut labore et dolore magna aliqua.</p></div>
    <div class="msg"><div class="msg-head"><span class="face" role="img" aria-label="Attendee photo"></span>Jhone Michel<time>6 min ago</time></div><p>Lorem ipsum dolor sit amet, consectetur ing elit, sed do eiusmod tempor incididunt ut labore et dolore magna aliqua.</p></div>
    <div class="msg"><div class="msg-head"><span class="face" role="img" aria-label="Attendee photo"></span>Jhone Michel<time>6 min ago</time></div><p>Lorem ipsum dolor sit amet, consectetur ing elit, sed do eiusmod tempor incididunt ut labore et dolore magna aliqua.</p></div>
    <div class="msg"><div class="msg-head"><span class="face" role="img" aria-label="Attendee photo"></span>Jhone Michel<time>6 min ago</time></div><p>Lorem ipsum dolor sit amet, consectetur ing elit, sed do eiusmod tempor incididunt ut labore et dolore magna aliqua.</p></div>
    <div class="composer"><span>Start Typing</span><b><svg viewBox="0 0 14 14"><path d="M13 1L1 6l5 2 2 5zM6 8l7-7"/></svg></b></div>
  </div>
  <div class="copy">© Copyrights.2020.The Company name</div>
</section>

<!-- Exhibition view -->
<section class="app app-3">
  <aside class="sidebar">
    <div class="brand">NEXAVENT<span class="mark"></span></div>
    <div class="rule"></div>
    <div class="nav-title">MAIN NAVIGATION</div>
    <ul class="nav">
      <li><svg viewBox="0 0 34 32"><rect x="3" y="5" width="28" height="24" rx="2"/><path d="M3 11h28M10 2v6M24 2v6M9 16h3M16 16h3M23 16h3M9 22h3M16 22h3M23 22h3"/></svg>Event Info</li>
      <li><svg viewBox="0 0 34 32"><rect x="3" y="3" width="28" height="26"/><path d="M3 3c4 8 6 14 4 26M31 3c-4 8-6 14-4 26M17 13l2 4 4 .5-3 3 1 4-4-2-4 2 1-4-3-3 4-.5z"/></svg>Stage</li>
      <li><svg viewBox="0 0 34 32"><rect x="16" y="3" width="15" height="12"/><path d="M3 29h28M6 29v-9h22v9M5 20v-8l4-6 3 6M20 7l6 5"/></svg>Breakouts</li>
      <li class="active"><svg viewBox="0 0 34 32"><path d="M3 5l7 3v20l-7-3zM31 5l-7 3v20l7-3z"/><rect x="11" y="9" width="12" height="12"/><path d="M17 21v7M13 28h8"/></svg>Virtual Exhibition</li>
      <li><svg viewBox="0 0 34 32"><rect x="10" y="3" width="14" height="12"/><circle cx="17" cy="9" r="3"/><path d="M17 15v6M4 29l5-8h16l5 8z"/></svg>Booths</li>
      <li><svg viewBox="0 0 34 32"><path d="M11 3h12l-3 7h-6z"/><circle cx="17" cy="20" r="10"/><path d="M17 14l2 4 4 .5-3 3 1 4-4-2-4 2 1-4-3-3 4-.5z"/></svg>Rewards</li>
    </ul>
  </aside>
  <header class="topbar">
    <div class="tools">
      <div class="tool"><svg viewBox="0 0 24 24"><path d="M12 22a2.5 2.5 0 0 0 2.5-2.5h-5A2.5 2.5 0 0 0 12 22zm7-6V11a7 7 0 0 0-5.5-6.8V3a1.5 1.5 0 0 0-3 0v1.2A7 7 0 0 0 5 11v5l-2 2v1h18v-1z"/></svg><span class="badge">5</span></div>
      <div class="tool"><svg viewBox="0 0 24 24"><path d="M3 5h18v12H8l-5 4z"/></svg><span class="badge">8</span></div>
      <div class="user"><span class="avatar" role="img" aria-label="User profile photo"></span>Jane.s<span class="caret"></span></div>
    </div>
  </header>
  <div class="duration">Event Duration (Remaining HH:MM)</div>
  <div class="media media-expo" role="img" aria-label="Isometric illustration of an exhibition hall with booths and visitors"><span class="play dark"></span></div>
  <div class="caption">Lorem ipsum dolor sit amet, consectetur adipiscing elit, sed do eiusmod<br><a>Click Here</a></div>
  <div class="cta">Find Out More</div>
  <div class="copy">© Copyrights.2020.The Company name</div>
</section>

</body>
</html>
```